Private Investigation Business Card Design

I need a business card for a new private investigation company named Brisk Inquiries. I perform mainly surveillance jobs, vehicle repossessions, document serves etc. The final design should aim for a professional look. The logo has a magnifying glass with stick man arms and legs and is in a running action to show the "Brisk" aspect of the name. If the colour scheme could remain the same as the website www.briskinquiries-demo.com.au with silvers,blacks and a couple electric blue highlights.
Industry/Entity Type
Business
Contact Information for Business Card
Morgan Kellaway
Brisk Inquiries
0487316204
PO Box 58, Carnwell NSW 2291
info@briskinquiries-demo.com.au
www.briskinquiries-demo.com.au
Look and feel

```html
<!DOCTYPE html>
<html lang="en">
<head>
<meta charset="utf-8">
<title>Brisk Inquiries – Business Card</title>
<link rel="stylesheet" href="https://fonts.googleapis.com/css2?family=Lato:wght@400;700;900&display=swap">
<style>
  :root {
    --backdrop: #e4e4e4;
    --card-front: #fbfbfb;
    --card-back: #3d3e40;
    --ink: #4a4a4a;
    --ink-soft: #3c3c3c;
    --rule: #5a5a5a;
    --mark-light: #8e8f92;
    --mark-dark: #a9aaad;
  }
  * { margin: 0; padding: 0; box-sizing: border-box; }
  html, body { width: 1200px; height: 720px; overflow: hidden; }
  body {
    background: var(--backdrop);
    font-family: "Lato", Arial, sans-serif;
    position: relative;
  }
  .card {
    position: absolute;
    top: 241px;
    width: 420px;
    height: 240px;
    border-radius: 8px;
  }
  .card--front { left: 148px; background: var(--card-front); }
  .card--back { left: 633px; background: var(--card-back); }

  .brand {
    position: absolute;
    display: flex;
    align-items: center;
    gap: 8px;
    font-weight: 900;
    white-space: nowrap;
  }
  .card--front .brand {
    left: 26px; top: 108px;
    font-size: 22px;
    color: var(--mark-light);
  }
  .card--back .brand {
    left: 50%; top: 50%;
    transform: translate(-50%, -50%);
    font-size: 38px;
    color: var(--mark-dark);
  }
  .brand__dot {
    display: inline-block;
    border-radius: 50%;
    background: currentColor;
  }
  .card--front .brand__dot { width: 14px; height: 14px; }
  .card--back .brand__dot { width: 22px; height: 22px; }

  .divider {
    position: absolute;
    left: 208px; top: 56px;
    width: 2px; height: 140px;
    background: var(--rule);
  }
  .details {
    position: absolute;
    left: 214px; top: 56px;
    color: var(--ink-soft);
  }
  .details__name {
    font-size: 17px;
    font-weight: 700;
    color: var(--ink);
    line-height: 20px;
  }
  .details__role { font-size: 12.5px; line-height: 16px; }
  .details__address {
    margin-top: 20px;
    font-size: 12.5px;
    line-height: 14px;
  }
  .details__contacts {
    list-style: none;
    margin-top: 11px;
    font-size: 12.5px;
    line-height: 13.5px;
  }
  .details__contacts li { display: flex; align-items: center; gap: 4px; }
  .details__contacts svg { width: 11px; height: 11px; flex: none; }
</style>
</head>
<body>
  <section class="card card--front" aria-label="Card front">
    <div class="brand"><span>Brisk Inquiries</span><span class="brand__dot"></span></div>
    <div class="divider"></div>
    <div class="details">
      <p class="details__name">Morgan Kellaway</p>
      <p class="details__role">Director</p>
      <p class="details__address">PO Box 58<br>Carnwell NSW 2291</p>
      <ul class="details__contacts">
        <li>
          <svg viewBox="0 0 12 12" aria-hidden="true"><path fill="#444" d="M1 3c0-1 1-2 2-2h6c1 0 2 1 2 2v1H8V3H4v1H1zM2 5h8l1 6H1z"/></svg>
          0487316204
        </li>
        <li>
          <svg viewBox="0 0 12 12" aria-hidden="true"><rect x="0.5" y="2" width="11" height="8" fill="#444"/><path d="M1 2.5l5 4 5-4" stroke="#fff" fill="none" stroke-width="1"/></svg>
          info@briskinquiries-demo.com.au
        </li>
        <li>
          <svg viewBox="0 0 12 12" aria-hidden="true"><rect x="1" y="2" width="10" height="7" fill="none" stroke="#444" stroke-width="1.2"/><rect x="4" y="10" width="4" height="1.2" fill="#444"/></svg>
          www.briskinquiries-demo.com.au
        </li>
      </ul>
    </div>
  </section>

  <section class="card card--back" aria-label="Card back">
    <div class="brand"><span>Brisk Inquiries</span><span class="brand__dot"></span></div>
  </section>
</body>
</html>
```